Medical Implant company needs a Top Quality Premium Brochure

We need to create a top quality brochure for VIP clients, formed by top spine surgeons. The main goal here is to cause a deep quality impact, positioning the company and it´s solutions above the others, with a refined, unique and creative material.

Special paper, hot stamping, innovative format are welcome.

For more information check out our website: www.corvalento.com.br (web translator are recommended for content understanding)

Corvalento works with top quality spine and pain management products, providing solutions for the medical specialists, investing in high quality processes and continued medical education.

Short briefing:
1 - Company profile
2 - Quality / vision
3 - Continued education programs
4 - Main products
5 - Main partners
6 - Final stuff (creative final thoughts / considerations)

FORMAT: 25 x 18,5 cm (horizontal)
PAGES - 16

REFERENCES:

https://www.folioquarry.net/gallery/52930184/Medical-Healthcare-Profile-Brochure

https://www.folioquarry.net/gallery/7719046/TK-Alpine-Style-Brochure

Target Market(s)

Mainly brazilian spine and neuro surgeons with minimally invasive surgery skills.

Industry/Entity Type

Education

Requirements
Must have

• 18 pages design

1. Cover
2. IMAGE + TITLE - About Us
3. IMAGE + TEXT - About Us
4. IMAGE + TITLE - Vision
5. IMAGE + TEXT - Vision
6. IMAGE + TITLE - Quality
7. IMAGE + TEXT - Quality
8. Timeline Left
9. Timeline Right
10. IMAGE + TITLE - Medical Education
11. IMAGE + TEXT - Medical Education
12. IMAGE + TITLE - Minimally Invasive Technology
13. IMAGE + TEXT - Minimally Invasive Technology
14. IMAGE + TITLE - Impact Phrase
15. IMAGE + TEXT - Impact Phrase
16. Back

As longs as the text is under development and will be placed internally in the winning design, please use 'lorem ipsum' for text areas. The titles can follow the index above.

Nice to have
• The use of office pictures with some style / artistic finish in pages "about us"

```html
<!DOCTYPE html>
<html lang="en">
<head>
<meta charset="utf-8">
<title>Corvalento – About Us</title>
<link rel="stylesheet" href="https://fonts.googleapis.com/css2?family=Raleway:wght@200;300;600&display=swap">
<style>
  :root {
    --brand-blue: #1372ba;
    --photo-light: #d6e2e4;
    --photo-mid: #b9cace;
    --photo-dark: #8fa3a9;
    --text-white: #ffffff;
    --title-grey: #7d7f82;
  }
  * { margin: 0; padding: 0; box-sizing: border-box; }
  html, body {
    width: 1200px;
    height: 848px;
    overflow: hidden;
    background: var(--brand-blue);
  }
  .page {
    position: relative;
    width: 1200px;
    height: 848px;
    background: var(--brand-blue);
    font-family: "Raleway", "Century Gothic", sans-serif;
    color: var(--text-white);
  }
  .office-photo {
    position: absolute;
    left: 0;
    top: 67px;
    width: 1200px;
    height: 234px;
    background: linear-gradient(180deg, var(--photo-light) 0%, var(--photo-mid) 70%, var(--photo-dark) 100%);
  }
  .intro-copy {
    position: absolute;
    left: 439px;
    top: 333px;
    width: 680px;
    font-size: 14.6px;
    line-height: 18.4px;
  }
  .intro-copy p { margin-bottom: 18.4px; }
  .intro-copy .quote,
  .intro-copy .lead { font-weight: 300; }
  .intro-copy .highlight { font-weight: 600; }
  .section-title-band {
    position: absolute;
    left: 0;
    top: 728px;
    width: 940px;
    height: 72px;
    background: linear-gradient(90deg, #ffffff 0%, #ffffff 22%, rgba(255,255,255,0.55) 48%, rgba(255,255,255,0) 100%);
  }
  .section-title {
    position: absolute;
    left: 52px;
    top: 12px;
    font-size: 44px;
    font-weight: 200;
    color: var(--title-grey);
    letter-spacing: 0.5px;
    line-height: 48px;
  }
</style>
</head>
<body>
  <main class="page">
    <div class="office-photo" role="img" aria-label="Office photograph: brushed steel company name sign mounted on a pale glass wall"></div>

    <section class="intro-copy">
      <p class="quote">"There is no one who loves pain itself, who seeks after it and wants to have it, simply because it is pain..."</p>
      <p class="lead">Lorem Ipsum is simply dummy text of the printing and typesetting industry. Lorem Ipsum has been the industry's standard dummy text ever since the 1500s, when an unknown printer took a galley of type and scrambled it to make a type specimen book. It has survived not only five centuries, but also the leap into electronic typesetting, remaining essentially unchanged. It was popularised in the 1960s with the release of Glyphset sheets containing Lorem Ipsum passages, and more recently with desktop publishing software like Orrin PageSmith including versions of Lorem Ipsum.</p>
      <p class="highlight">It is a long established fact that a reader will be distracted by the readable content of a page when looking at its layout. The point of using Lorem Ipsum is that it has a more-or-less normal distribution of letters, as opposed to using 'Content here, content here', making it look like readable English. Many desktop publishing packages and web page editors now use Lorem Ipsum as their default model text, and a search for 'lorem ipsum' will uncover many web sites still in their infancy. Various versions have evolved over the years, sometimes by accident, sometimes on purpose (injected humour and the like).</p>
    </section>

    <div class="section-title-band">
      <h1 class="section-title">About Us</h1>
    </div>
  </main>
</body>
</html>
```